Brookmere Osteopathy flyer

I want a clean clear DL flyer (but also want an A4 poster) promoting a new Osteopathic business in a semi rural area in Tasmania (Australia).
It can have pictures like the examples attached to show people what Osteopathy is (its like Chiropractic and physiotherapy).
I am the sole practioner and am male, so any pictures would be best to be a white male if possible.
I've attached some wording, you can use all, or none of it
I don't have a phone number for the business yet
info@brookmereosteopathy.example
www.brookmereosteopathy.example
Target Market(s)
Australians, from tradies, professionals, babies to retired people
Industry/Entity Type
Health
Look and feel

```html
<!DOCTYPE html>
<html lang="en">
<head>
<meta charset="utf-8">
<title>Brookmere Osteopathy flyer</title>
<link href="https://fonts.googleapis.com/css2?family=Open+Sans:wght@700&family=Poppins:wght@300;400&display=swap" rel="stylesheet">
<style>
  :root {
    --page-bg: #b0b0b0;
    --paper: #ecebeb;
    --white: #ffffff;
    --blue: #0e93cf;
    --blue-deep: #0988c2;
    --blue-light: #e3f3fc;
    --orange: #e87a1e;
    --ink: #1f1f1f;
    --contact-ink: #d6f0ff;
    --icon-ink: #7fcdf2;
  }
  * { margin: 0; padding: 0; box-sizing: border-box; }
  html, body { width: 895px; height: 1200px; overflow: hidden; background: var(--page-bg); }

  .flyer {
    position: absolute; left: 117px; top: 104px;
    width: 661px; height: 992px; overflow: hidden;
    background: var(--paper);
    font-family: "Poppins", sans-serif; color: var(--ink);
  }
  .flyer-shapes { position: absolute; inset: 0; width: 661px; height: 992px; }

  .brand {
    position: absolute; left: 51px; top: 8px; width: 111px; height: 111px;
    border: 2px solid var(--blue); border-radius: 50%;
    display: flex; align-items: center; justify-content: center; text-align: center;
    font-weight: 400; font-size: 13px; line-height: 1.3; color: var(--blue);
  }

  .reasons-banner {
    position: absolute; left: 0; top: 453px; width: 368px; height: 64px;
    background: var(--blue); border-radius: 0 32px 32px 0;
    display: flex; align-items: center; padding-left: 18px;
    font-family: "Open Sans", sans-serif; font-weight: 700; font-size: 12.2px;
    color: var(--white); white-space: nowrap;
  }

  .reasons { position: absolute; top: 0; list-style: none; }
  .reasons-left { left: 39px; }
  .reasons-right { left: 343px; }
  .reasons li {
    position: absolute; left: 0; white-space: nowrap;
    display: flex; align-items: center; transform: translateY(-50%);
    font-weight: 300; font-size: 14.6px; line-height: 1;
  }
  .tick { width: 24px; height: 22px; margin-right: 7px; flex: none; }
  .tick-orange circle { fill: var(--orange); }
  .tick-blue circle { fill: var(--blue); }

  .summary {
    position: absolute; left: 30px; top: 740px; width: 545px;
    text-align: center; font-weight: 300; font-size: 11.4px; line-height: 17px;
  }

  .contacts { position: absolute; left: 36px; top: 0; list-style: none; }
  .contacts li {
    position: absolute; left: 0; white-space: nowrap; transform: translateY(-50%);
    display: flex; align-items: center; gap: 8px;
    font-weight: 300; font-size: 11px; color: var(--contact-ink);
  }
  .contacts svg { width: 14px; height: 14px; flex: none; }
</style>
</head>
<body>
<div class="flyer">
  <svg class="flyer-shapes" viewBox="0 0 1220 1830" preserveAspectRatio="none">
    <defs>
      <linearGradient id="treatmentTone" x1="0" y1="0" x2="0.4" y2="1">
        <stop offset="0" stop-color="#f1f0ef"/>
        <stop offset="0.45" stop-color="#d8c2b4"/>
        <stop offset="0.75" stop-color="#4a4a52"/>
        <stop offset="1" stop-color="#a9c3e6"/>
      </linearGradient>
      <radialGradient id="portraitTone" cx="0.5" cy="0.55" r="0.6">
        <stop offset="0" stop-color="#f3f6f9"/>
        <stop offset="0.6" stop-color="#e2ebf3"/>
        <stop offset="1" stop-color="#ffffff"/>
      </radialGradient>
      <linearGradient id="backTone" x1="0" y1="0" x2="1" y2="1">
        <stop offset="0" stop-color="#efe3da"/>
        <stop offset="0.5" stop-color="#e3b698"/>
        <stop offset="1" stop-color="#c98f6c"/>
      </linearGradient>
      <clipPath id="portraitClip"><circle cx="948" cy="800" r="207"/></clipPath>
    </defs>

    <path role="img" aria-label="Osteopath stretching a patient's arm and shoulder as she lies on a treatment table"
      fill="url(#treatmentTone)"
      d="M0,330 C260,250 560,200 640,0 L1220,0 L1220,940 L1000,740 C700,745 300,700 0,520 Z"/>
    <path fill="var(--white)" d="M0,0 H640 C570,170 340,250 0,330 Z"/>
    <path fill="none" stroke="var(--orange)" stroke-width="13" d="M0,338 C170,260 520,230 605,60"/>
    <path fill="none" stroke="var(--orange)" stroke-width="14" d="M0,520 C180,670 420,735 730,745"/>

    <path fill="var(--orange)" d="M1110,880 C1160,920 1200,960 1220,990 L1220,1085 C1185,1030 1140,975 1090,935 Z"/>

    <circle cx="948" cy="800" r="228" fill="var(--blue-light)" stroke="var(--blue)" stroke-width="3"/>
    <circle role="img" aria-label="Portrait of the practitioner in a white coat with a stethoscope, arms folded"
      cx="948" cy="800" r="207" fill="url(#portraitTone)"/>

    <path role="img" aria-label="Hands massaging a patient's upper back and shoulder"
      fill="url(#backTone)"
      d="M594,1663 C760,1560 960,1520 1080,1490 C1170,1460 1210,1330 1220,1190 L1220,1830 L829,1830 C760,1760 680,1700 594,1663 Z"/>
    <path fill="none" stroke="var(--orange)" stroke-width="3" d="M594,1663 C760,1560 960,1520 1080,1490 C1170,1460 1210,1330 1220,1190"/>

    <path fill="none" stroke="var(--blue)" stroke-width="8" d="M0,1512 C300,1532 520,1610 628,1690"/>
    <path fill="var(--blue-deep)" d="M0,1540 C300,1570 650,1660 829,1830 L0,1830 Z"/>
  </svg>

  <div class="brand">Brookmere<br>Osteopathy</div>

  <div class="reasons-banner">COMMON REASONS PEOPLE VISIT AN OSTEOPATH</div>

  <ul class="reasons reasons-left">
    <li style="top:574px"><svg class="tick tick-orange" viewBox="0 0 24 22"><circle cx="10" cy="12" r="10"/><path d="M5,12 l4,4 L22,2" fill="none" stroke="#fff" stroke-width="1.8"/></svg>Back / neck pain</li>
    <li style="top:601px"><svg class="tick tick-orange" viewBox="0 0 24 22"><circle cx="10" cy="12" r="10"/><path d="M5,12 l4,4 L22,2" fill="none" stroke="#fff" stroke-width="1.8"/></svg>Headaches / migraines</li>
    <li style="top:633px"><svg class="tick tick-orange" viewBox="0 0 24 22"><circle cx="10" cy="12" r="10"/><path d="M5,12 l4,4 L22,2" fill="none" stroke="#fff" stroke-width="1.8"/></svg>Joint and muscle pain</li>
    <li style="top:660px"><svg class="tick tick-orange" viewBox="0 0 24 22"><circle cx="10" cy="12" r="10"/><path d="M5,12 l4,4 L22,2" fill="none" stroke="#fff" stroke-width="1.8"/></svg>Pregnancy-related discomfort</li>
    <li style="top:692px"><svg class="tick tick-orange" viewBox="0 0 24 22"><circle cx="10" cy="12" r="10"/><path d="M5,12 l4,4 L22,2" fill="none" stroke="#fff" stroke-width="1.8"/></svg>Disc related issues</li>
  </ul>

  <ul class="reasons reasons-right">
    <li style="top:574px"><svg class="tick tick-blue" viewBox="0 0 24 22"><circle cx="10" cy="12" r="10"/><path d="M5,12 l4,4 L22,2" fill="none" stroke="#fff" stroke-width="1.8"/></svg>Sciatica</li>
    <li style="top:601px"><svg class="tick tick-blue" viewBox="0 0 24 22"><circle cx="10" cy="12" r="10"/><path d="M5,12 l4,4 L22,2" fill="none" stroke="#fff" stroke-width="1.8"/></svg>Plantar fasciitis</li>
    <li style="top:633px"><svg class="tick tick-blue" viewBox="0 0 24 22"><circle cx="10" cy="12" r="10"/><path d="M5,12 l4,4 L22,2" fill="none" stroke="#fff" stroke-width="1.8"/></svg>Tendonitis / Bursitis</li>
    <li style="top:660px"><svg class="tick tick-blue" viewBox="0 0 24 22"><circle cx="10" cy="12" r="10"/><path d="M5,12 l4,4 L22,2" fill="none" stroke="#fff" stroke-width="1.8"/></svg>Adhesive capsulitis (frozen shoulder)</li>
    <li style="top:692px"><svg class="tick tick-blue" viewBox="0 0 24 22"><circle cx="10" cy="12" r="10"/><path d="M5,12 l4,4 L22,2" fill="none" stroke="#fff" stroke-width="1.8"/></svg>Tennis / Golfers elbow</li>
  </ul>

  <p class="summary">Osteopaths use a combination of joint manipulation, targeted deep tissue massage and stretching to improve function, relieve pain and support the body’s ability to heal itself.</p>

  <ul class="contacts">
    <li style="top:896px"><svg viewBox="0 0 14 14"><path d="M7,1 a4.5,4.5 0 0 1 4.5,4.5 C11.5,9 7,13.5 7,13.5 C7,13.5 2.5,9 2.5,5.5 A4.5,4.5 0 0 1 7,1 Z" fill="var(--icon-ink)"/><circle cx="7" cy="5.5" r="1.6" fill="var(--blue-deep)"/></svg>24 Mill Creek Road, Brookmere</li>
    <li style="top:942px"><svg viewBox="0 0 14 14"><g fill="none" stroke="var(--icon-ink)" stroke-width="1"><circle cx="7" cy="7" r="6"/><ellipse cx="7" cy="7" rx="2.6" ry="6"/><path d="M1,7 H13 M2,4 H12 M2,10 H12"/></g></svg>www.brookmereosteopathy.example</li>
    <li style="top:965px"><svg viewBox="0 0 14 14"><rect x="1" y="3" width="12" height="8.5" fill="var(--icon-ink)"/><path d="M1,3 L7,8 L13,3" fill="none" stroke="var(--blue-deep)" stroke-width="1"/></svg>info@brookmereosteopathy.example</li>
  </ul>
</div>
</body>
</html>
```